Bicycle Tour Schedule on a Business Card

Need to develop a 2 side business card that highlights a series of bike tours on 1 side and a series of events on the other side.
This will be inserted into a card wallet that attaches to a cell phone and will be handed out at an expo. The card wallets are black and red so color must coordinate with both. There is a photo of the card wallets attached.

1 side needs to be devoted to Pedal Vista Trek and the others to KQR Venture events on the other. Dates and websites are very important.

Target Market(s)

Cyclists
Predominantly men ages 40+
Educated, Professionals

Industry/Entity Type

Business

Font styles to use
Serif

Requirements
Must have
• Pedal vista treks logo on 1 side and KQR Venture logo on the other side
• dates and websites clearly visible
• Design of both sides must go together.
• Must be portrait not landscape

```html
<!DOCTYPE html>
<html lang="en">
<head>
<meta charset="utf-8">
<title>Pedal Vista Treks and KQR Venture Event Cards</title>
<link href="https://fonts.googleapis.com/css2?family=Open+Sans:ital,wght@0,400;0,600;0,700;1,700&display=swap" rel="stylesheet">
<style>
  :root {
    --backdrop: #e9e4dc;
    --card: #ffffff;
    --tour-blue: #1f6db3;
    --tour-green: #4fb553;
    --tour-green-soft: #e6f4e4;
    --event-red: #d0213b;
    --event-blue: #2a8fc4;
    --event-red-soft: #fbe7ea;
    --card-shadow: 0 10px 28px rgba(40, 30, 20, 0.28);
  }
  * { box-sizing: border-box; margin: 0; padding: 0; }
  html, body {
    width: 1200px; height: 950px; overflow: hidden;
    background: var(--backdrop);
    font-family: "Open Sans", Arial, sans-serif;
  }
  .card-pair {
    position: relative; width: 1200px; height: 950px;
    display: flex; justify-content: center; align-items: center; gap: 80px;
  }
  .card {
    position: relative; width: 400px; height: 680px;
    background: var(--card); box-shadow: var(--card-shadow);
    overflow: hidden; text-align: center;
    padding: 56px 36px 40px;
  }
  .card > *:not(.card-backdrop) { position: relative; }
  .card-backdrop { position: absolute; inset: 0; }

  /* Tours side */
  .tour-brand {
    display: flex; align-items: center; justify-content: center; gap: 12px;
    color: var(--tour-green); font-weight: 700; font-size: 34px;
    line-height: 1.1; margin-bottom: 34px;
  }
  .tour-brand .brand-dot {
    width: 26px; height: 26px; border-radius: 50%; background: var(--tour-blue);
    flex: none;
  }
  .tour-tagline {
    color: var(--tour-blue); font-weight: 700; font-style: italic;
    font-size: 22px; line-height: 1.3; margin-bottom: 34px;
  }
  .tour-list { list-style: none; }
  .tour-item { margin-bottom: 18px; }
  .tour-name { color: var(--tour-blue); font-size: 21px; line-height: 1.25; }
  .tour-dates { color: var(--tour-green); font-size: 21px; font-weight: 700; line-height: 1.25; }

  /* Events side */
  .event-brand {
    display: flex; align-items: center; justify-content: center; gap: 12px;
    color: var(--event-red); font-weight: 700; font-size: 34px;
    line-height: 1.1; margin: 20px 0 28px;
  }
  .event-brand .brand-square {
    width: 26px; height: 26px; background: var(--event-red); flex: none;
  }
  .event-series {
    color: var(--event-red); font-weight: 700; font-size: 22px;
    line-height: 1.25; margin-bottom: 22px;
  }
  .event-list { list-style: none; }
  .event-item { margin-bottom: 16px; }
  .event-name { color: var(--event-blue); font-size: 19px; line-height: 1.25; }
  .event-dates, .event-site {
    color: var(--event-red); font-size: 19px; font-weight: 700; line-height: 1.25;
  }
</style>
</head>
<body>
<main class="card-pair">

  <section class="card card-tours" aria-label="Pedal Vista Treks tour schedule">
    <svg class="card-backdrop" viewBox="0 0 400 680" aria-hidden="true">
      <circle cx="130" cy="560" r="150" fill="var(--tour-green-soft)"/>
    </svg>
    <h1 class="tour-brand"><span class="brand-dot"></span>Pedal Vista Treks</h1>
    <p class="tour-tagline">Fully supported bike tours.<br>Discover the hidden gems on two wheels</p>
    <ul class="tour-list">
      <li class="tour-item"><div class="tour-name">Heart of Colorado</div><div class="tour-dates">June 26 - July 2, 2016</div></li>
      <li class="tour-item"><div class="tour-name">Colorado Front Range Tour</div><div class="tour-dates">August 14-20, 2016</div></li>
      <li class="tour-item"><div class="tour-name">Cape Cod Tour</div><div class="tour-dates">October 9-15, 2016</div></li>
      <li class="tour-item"><div class="tour-name">Florida Key Tours</div><div class="tour-dates">November 6-12, 2016 &amp;<br>December 4-10, 2016</div></li>
    </ul>
  </section>

  <section class="card card-events" aria-label="KQR Venture event schedule">
    <svg class="card-backdrop" viewBox="0 0 400 680" aria-hidden="true">
      <rect x="60" y="360" width="300" height="300" rx="60" fill="var(--event-red-soft)"/>
    </svg>
    <h2 class="event-brand"><span class="brand-square"></span>KQR Venture</h2>
    <p class="event-series">Trio Wheel Series:<br>Cycling camps for youth</p>
    <ul class="event-list">
      <li class="event-item"><div class="event-name">Mountain Bike Camp</div><div class="event-dates">July 8-10, 2016</div></li>
      <li class="event-item"><div class="event-name">Cyclocross Camp</div><div class="event-dates">August 26-28, 2016</div><div class="event-site">Triowheelseries.org</div></li>
      <li class="event-item"><div class="event-name">Summit Century Ride</div><div class="event-dates">June 18, 2016</div><div class="event-site">Summitcenturyride.com</div></li>
      <li class="event-item"><div class="event-name">Ridge 2 Ridge Challenge</div><div class="event-dates">July 30, 2016 - Ridge2ridge.com</div></li>
      <li class="event-item"><div class="event-name">Zany Pedal Ride</div><div class="event-dates">September 11, 2016</div><div class="event-site">zanypedalride.com</div></li>
    </ul>
  </section>

</main>
</body>
</html>
```